Wix Design for a Clothing Design Web Marketing Site

We need a Wix design and content (including any images and copy) for a clothing design web storefront, Sew To Suit (or sewtosuit). Rough ideas and content can be found at http://marenvoltis.wix.com/sewtosuit.

Sew To Suit is an innovative business concept that combines fashion and entertainment. The business model allows customers to actively participate in the creation of fashion designs/concepts , visualize the garment in the customer’s body in 3D, and buy the physical garment made specially to fit the customer.
The fashion consultant will be able to create the design based on client's desires and test various possibilities (size, fabric, cut, etc..) in front of the customer, using software Drapova (the software is a key component of this business model)
(when developing the website use images from Drapova)
After the design is created, the customer can choose to order the actual piece. The garment will be made according to the created design, the customer measurements.

Target Market(s)

Primarily women from 25 to 45, who are fashion enthusiasts and appreciate fit and exclusivity. They are hedonistic shoppers, who shop for entertainment.
Men (metrosexuals) who are fashion enthusiasts, also hedonistic shoppers.

Industry/Entity Type

Clothing

Font styles to use
Serif
Sans Serif

Requirements
Must have
• Must have a landing page (home) or section, that gives the consumer an idea of what Sew To Suit will do for them, an about page or section that tells about the company and product, a how it works page or section that describes how it works (http://marenvoltis.wix.com/sewtosuit#!services3/c192y), and page or section about pricing, and a page or section on how to contact us.
Nice to have
• Very modern and clean. The website must be based on the main picture of the studio in the example. If that studio is the store, what will the website look like?
• Colors yellow, grey and white. Use the zig zag in yellow and white. You can change the size of the lines. The zig zagi gives the modern and bold accent. Outfits in pictures must show nicely tailored garments.

```html
<!DOCTYPE html>
<html lang="en">
<head>
<meta charset="utf-8">
<title>Sew To Suit — Home</title>
<link href="https://fonts.googleapis.com/css2?family=Lora:ital,wght@0,400;0,700;1,400&display=swap" rel="stylesheet">
<style>
  :root{
    --ink:#000;
    --paper:#fff;
    --accent:#f2f21a;
    --accent-deep:#c9cc1c;
    --heading:#4a4545;
    --text:#2b2b2b;
    --sepia-light:#b3a8a3;
    --sepia-mid:#8a7e79;
    --sepia-dark:#5e5450;
    --sepia-deep:#463e3b;
  }
  *{box-sizing:border-box;margin:0;padding:0}
  html,body{width:965px;height:1200px;overflow:hidden;background:var(--ink)}
  body{font-family:'Lora',Georgia,serif;color:var(--text);position:relative}

  .site-header{position:absolute;left:0;top:0;width:965px;height:196px;background:var(--ink)}
  .brand-frame{position:absolute;left:414px;top:17px;width:137px;height:109px;border:1px solid #bbb;display:flex;align-items:center;justify-content:center}
  .brand-name{font-family:'Lora',Georgia,serif;font-weight:700;font-size:17px;color:var(--accent);letter-spacing:.3px}
  .main-nav{position:absolute;top:152px;left:0;width:965px;display:flex;justify-content:center}
  .main-nav a{font-size:10.5px;color:var(--paper);text-decoration:none;padding:0 13.5px;line-height:18px;border-left:1px solid var(--paper)}
  .main-nav a:first-child{border-left:none}
  .main-nav a.is-active{color:var(--accent)}

  .edge{position:absolute;left:0;width:965px;height:5px;z-index:3}

  .photo{position:absolute}
  .panel{position:absolute;background:var(--paper)}
  .pointer{position:absolute;z-index:2}

  .hero-photo-left{left:0;top:196px;width:482px;height:317px;
    background:
      radial-gradient(ellipse 140px 160px at 200px 250px,rgba(196,186,181,.75),transparent 70%),
      radial-gradient(ellipse 160px 120px at 120px 60px,rgba(70,62,59,.7),transparent 70%),
      radial-gradient(ellipse 130px 140px at 420px 110px,rgba(210,202,198,.6),transparent 70%),
      linear-gradient(135deg,var(--sepia-light),var(--sepia-mid) 50%,var(--sepia-dark))}
  .hero-photo-right{left:794px;top:196px;width:171px;height:317px;
    background:
      radial-gradient(ellipse 90px 80px at 120px 270px,rgba(196,186,181,.7),transparent 70%),
      radial-gradient(ellipse 110px 140px at 60px 90px,rgba(70,62,59,.75),transparent 70%),
      linear-gradient(160deg,var(--sepia-mid),var(--sepia-dark))}
  .hero-panel{left:482px;top:196px;width:312px;height:317px}
  .hero-panel .welcome{position:absolute;left:37px;top:46px;font-size:40px;font-weight:400;color:var(--heading);line-height:1}
  .hero-panel .title{position:absolute;left:37px;top:93px;font-size:45px;font-weight:700;color:var(--heading);line-height:1;white-space:nowrap}
  .hero-panel .title em{font-style:normal;color:var(--accent-deep)}
  .hero-panel .tagline{position:absolute;left:37px;top:164px;font-size:17px;font-style:italic;color:var(--heading);line-height:27px}
  .btn-read{position:absolute;left:37px;top:247px;width:129px;height:34px;background:var(--ink);border:1px solid var(--accent);color:var(--accent);font-size:12.5px;font-weight:700;display:flex;align-items:center;justify-content:center;text-decoration:none}

  .steps-photo-left{left:0;top:513px;width:117px;height:489px;
    background:
      radial-gradient(ellipse 60px 130px at 30px 280px,rgba(70,62,59,.8),transparent 70%),
      radial-gradient(ellipse 70px 120px at 90px 120px,rgba(196,186,181,.6),transparent 70%),
      linear-gradient(180deg,var(--sepia-dark),var(--sepia-mid))}
  .steps-photo-right{left:482px;top:513px;width:483px;height:489px;
    background:
      radial-gradient(ellipse 150px 90px at 240px 50px,rgba(70,62,59,.75),transparent 70%),
      radial-gradient(ellipse 110px 230px at 120px 330px,rgba(222,214,210,.7),transparent 70%),
      radial-gradient(ellipse 110px 220px at 410px 330px,rgba(70,62,59,.6),transparent 70%),
      radial-gradient(ellipse 90px 90px at 270px 250px,rgba(94,84,80,.5),transparent 70%),
      linear-gradient(135deg,var(--sepia-light),var(--sepia-mid) 50%,var(--sepia-dark))}
  .steps-panel{left:117px;top:513px;width:365px;height:489px}
  .steps{position:absolute;left:42px;top:32px;list-style:none}
  .step h3{font-size:18px;font-weight:700;color:var(--text);line-height:24px}
  .step p{font-size:10.5px;line-height:23px;color:var(--text)}
  .step{margin-bottom:13px}

  .site-footer{position:absolute;left:0;top:1002px;width:965px;height:198px;background:var(--ink);color:var(--paper)}
  .footer-brand{position:absolute;left:79px;top:64px;display:flex;align-items:center;gap:8px}
  .footer-brand .mark{width:14px;height:14px;background:var(--accent)}
  .footer-brand .brand-name{font-size:16px}
  .footer-nav{position:absolute;left:222px;top:69px;display:flex}
  .footer-nav a{font-size:11px;color:var(--paper);text-decoration:none;padding:0 9px;border-left:1px solid var(--paper);line-height:14px}
  .footer-nav a:first-child{padding-left:0;border-left:none}
  .contact{position:absolute;right:79px;top:38px;list-style:none;text-align:right}
  .contact li{font-size:10.5px;line-height:21.5px;display:flex;justify-content:flex-end;align-items:center;gap:7px}
  .contact svg{fill:var(--accent)}
  .footer-rule{position:absolute;left:0;top:150px;width:965px;height:1px;background:#222}
  .copyright{position:absolute;top:166px;left:0;width:965px;text-align:center;font-size:10.5px}
  .social{position:absolute;left:808px;top:168px;display:flex;gap:9px}
  .social span{width:13px;height:13px;border-radius:50%;background:var(--paper)}
</style>
</head>
<body>
  <header class="site-header">
    <div class="brand-frame"><span class="brand-name">Sew To Suit</span></div>
    <nav class="main-nav">
      <a href="#" class="is-active">HOME</a>
      <a href="#">WHAT IS SEW TO SUIT?</a>
      <a href="#">HOW IS WORKS</a>
      <a href="#">PRICE</a>
      <a href="#">CONTACT US</a>
    </nav>
  </header>

  <svg class="edge" style="top:192px" viewBox="0 0 965 5" preserveAspectRatio="none" aria-hidden="true">
    <defs><pattern id="teeth-top" width="6" height="5" patternUnits="userSpaceOnUse"><path d="M0 5 L3 0 L6 5Z" fill="#fff"/></pattern></defs>
    <rect width="965" height="5" fill="url(#teeth-top)"/>
  </svg>

  <section class="hero">
    <div class="photo hero-photo-left" role="img" aria-label="Sepia fashion photo of a couple in tailored clothes among leaves"></div>
    <div class="panel hero-panel">
      <h1 class="welcome">Welcome to</h1>
      <h2 class="title">Sew <em>To</em> Suit</h2>
      <p class="tagline">Clothes made specially for you<br>and designed by you.</p>
      <a href="#" class="btn-read">READ MORE »</a>
    </div>
    <svg class="pointer" style="left:446px;top:334px" width="37" height="36" viewBox="0 0 37 36" aria-hidden="true"><path d="M37 0 L0 18 L37 36Z" fill="#fff"/></svg>
    <div class="photo hero-photo-right" role="img" aria-label="Sepia fashion photo continuing the studio scene"></div>
  </section>

  <section class="how-it-works">
    <div class="photo steps-photo-left" role="img" aria-label="Sepia photo detail of leaves and shadows"></div>
    <div class="panel steps-panel">
      <ul class="steps">
        <li class="step"><h3>Be Inspired</h3><p>Be inspired by the latest trends, iconic styles from all eras<br>and the most prestigious fashion shows</p></li>
        <li class="step"><h3>Design</h3><p>Learn about our unique process, &nbsp;where you<br>become the designer</p></li>
        <li class="step"><h3>Choose the Fabric</h3><p>First rate fabrics &amp; highest<br>quality materials</p></li>
        <li class="step"><h3>See your Creation</h3><p>See your creation in 3D</p></li>
        <li class="step"><h3>Wear it</h3><p>Wear your design, fitted for your exact body<br>measurements</p></li>
        <li class="step"><h3>Have Fun, Be Creative</h3><p>The thrilling experience of creating</p></li>
      </ul>
    </div>
    <svg class="pointer" style="left:482px;top:713px" width="37" height="34" viewBox="0 0 37 34" aria-hidden="true"><path d="M0 0 L37 17 L0 34Z" fill="#fff"/></svg>
    <div class="photo steps-photo-right" role="img" aria-label="Sepia fashion photo of a woman in sunglasses and a man in a patterned shirt"></div>
  </section>

  <svg class="edge" style="top:999px" viewBox="0 0 965 5" preserveAspectRatio="none" aria-hidden="true">
    <defs><pattern id="teeth-bottom" width="6" height="5" patternUnits="userSpaceOnUse"><path d="M0 0 L3 5 L6 0Z" fill="#fff"/></pattern></defs>
    <rect width="965" height="5" fill="url(#teeth-bottom)"/>
  </svg>

  <footer class="site-footer">
    <div class="footer-brand"><span class="mark"></span><span class="brand-name">Sew To Suit</span></div>
    <nav class="footer-nav">
      <a href="#">HOME</a>
      <a href="#">WHAT IS SEW TO SUIT?</a>
      <a href="#">MORE</a>
    </nav>
    <ul class="contact">
      <li><svg width="9" height="12" viewBox="0 0 9 12" aria-hidden="true"><path d="M4.5 0A4.5 4.5 0 0 0 0 4.5C0 8 4.5 12 4.5 12S9 8 9 4.5A4.5 4.5 0 0 0 4.5 0Zm0 6.3a1.8 1.8 0 1 1 0-3.6 1.8 1.8 0 0 1 0 3.6Z"/></svg>Marlow Bay, CA</li>
      <li><svg width="12" height="12" viewBox="0 0 12 12" aria-hidden="true"><path d="M2.4 0.5 4.3 3 3.2 4.6C3.9 6.1 5.9 8.1 7.4 8.8L9 7.7 11.5 9.6 10.3 11.5C5.4 11.3 0.7 6.6 0.5 1.7Z"/></svg>1-555-010-2468</li>
      <li><svg width="15" height="11" viewBox="0 0 15 11" aria-hidden="true"><path d="M0 0H15V1L7.5 6 0 1Z"/><path d="M0 2.6 7.5 7.6 15 2.6V11H0Z"/></svg>hello@sewtosuit.example</li>
    </ul>
    <div class="footer-rule"></div>
    <p class="copyright">@ 2015 Sew To Suit . All rights are reserved.</p>
    <div class="social" role="img" aria-label="Social media links"><span></span><span></span><span></span><span></span></div>
  </footer>
</body>
</html>
```